House flipping business web site needed

pinecrestholdingsgroup.example.
I am a residential developer in Northern NJ and I am looking for a fresh new updated website. I have an intro video about my company being made now. I don't update it very often but I want an easy format that I can add update photos to on projects I have worked on or homes I renovate for sale.

Target Market(s)

investors into my projects so a portfolio , people looking to sell their homes to me.

Industry/Entity Type

Real Estate Development

Number of Pages Required

4 page

Font styles to use
Serif

Colors
33b8a4
39a9d7
cadf82

Requirements
Must have
• space for an intro video about my company
• a portfolio with pictures and information about each project
• Markets we serve- Morris County, NJ
• My logo- already created
• SEO
• Yes I would like this to function over all platforms. Phone, computer, all platforms.
• history and background page
• I am looking for a completed page that I can upload to the site that hosts my website
Nice to have
• I want something creative, easy to navigate. modern.

```html
<!DOCTYPE html>
<html lang="en">
<head>
<meta charset="utf-8">
<title>Pinecrest Holdings Group — Builders and Renovators</title>
<link href="https://fonts.googleapis.com/css2?family=Roboto:wght@300;400;500;700&family=Caveat:wght@500&display=swap" rel="stylesheet">
<style>
:root{
  --blue:#3aa6e2;
  --blue-deep:#2f97d6;
  --blue-light:#86cdf5;
  --sky:#bfe4fa;
  --green:#8cc63f;
  --ink:#222;
  --muted:#555;
  --paper:#f4f5f6;
  --white:#fff;
}
*{box-sizing:border-box;margin:0;padding:0}
html,body{width:1200px;height:2568px;overflow:hidden}
body{font-family:"Roboto",Arial,sans-serif;color:var(--ink);background:var(--white);position:relative}
.abs{position:absolute}

/* header */
.topbar{left:0;top:0;width:1200px;height:34px;background:var(--white)}
.topbar .info{position:absolute;top:8px;left:590px;font-size:15px;color:#888;display:flex;gap:22px;align-items:center}
.tag{color:#fff;font-size:14px;font-weight:700;border-radius:6px;padding:2px 9px}
.tag.builders{background:var(--blue-deep)}
.tag.renovators{background:var(--green)}
.navband{left:0;top:34px;width:1200px;height:69px;background:linear-gradient(90deg,var(--blue) 0%,var(--blue-light) 100%)}
.nav{position:absolute;right:50px;top:22px;display:flex;gap:37px;font-size:18px;color:#fff}
.brand{left:53px;top:0;width:284px;height:115px;background:#fff;border-radius:0 0 12px 12px;box-shadow:0 2px 6px rgba(0,0,0,.12);display:flex;align-items:center;justify-content:center;gap:10px}
.brand .mark{width:34px;height:34px;border-radius:50%;background:var(--blue)}
.brand .name{font-size:22px;font-weight:500;color:var(--blue-deep);line-height:1.05}

/* hero */
.hero{left:0;top:103px;width:1200px;height:489px;background:linear-gradient(180deg,#8aa3b8 0%,#5d7a86 35%,#3b5a4e 62%,#2f8fb3 80%,#1f6f94 100%)}
.hero-title{right:12px;top:163px;text-align:right;font-family:"Caveat",cursive;color:#fff;font-size:52px;line-height:61px;letter-spacing:1px}
.btn-hero{top:403px;height:33px;background:var(--blue-deep);color:#fff;font-size:11px;font-weight:700;display:flex;align-items:center;justify-content:center;border-radius:2px}
.dots{left:566px;top:561px;display:flex;gap:10px}
.dots span{width:9px;height:9px;border-radius:50%;background:#fff}
.dots span.off{background:none;border:1px solid #fff}

/* welcome */
.welcome{left:0;top:592px;width:1200px;height:196px;background:linear-gradient(90deg,var(--blue) 0%,var(--blue-light) 100%);color:#fff;text-align:center}
.welcome h1{font-size:23px;font-weight:700;margin-top:15px}
.rule{border-top:2px dotted rgba(255,255,255,.7);margin:8px auto 0;width:1108px}
.welcome p{font-size:13.5px;line-height:20px;width:1080px;margin:14px auto 0}

/* builders */
.builders{left:0;top:788px;width:1200px;height:407px;background:var(--paper)}
.section-title{font-size:23px;font-weight:500;text-align:center;color:var(--ink)}
.section-title em{font-style:normal;color:var(--blue)}
.builders .section-title{margin-top:24px}
.rule-blue{border-top:2px dotted var(--blue);width:1108px;margin:10px auto 0}
.feature{top:105px;width:340px;text-align:center}
.feature .icon{width:75px;height:80px;margin:0 auto;background:linear-gradient(160deg,#5bb9ee,var(--blue-deep));display:flex;align-items:center;justify-content:center}
.feature h3{font-size:17px;font-weight:700;margin-top:12px}
.feature p{font-size:13px;line-height:19.5px;color:var(--muted);margin-top:16px}

/* mail + video */
.mail{left:0;top:1195px;width:601px;height:329px;background:linear-gradient(135deg,var(--blue-deep) 0%,var(--blue-light) 100%)}
.mail h2{color:#fff;font-size:27px;font-weight:500;text-align:center;margin-top:30px}
.field{position:absolute;background:#fff;border-radius:4px;color:#999;font-size:12px;display:flex;justify-content:center;align-items:center}
.send{left:225px;top:264px;width:136px;height:33px;background:#fff;border-radius:4px;font-size:13px;font-weight:500;display:flex;align-items:center;justify-content:center}
.video{left:601px;top:1195px;width:599px;height:329px;background:linear-gradient(180deg,#8fb4d6 0%,#c9d8e4 35%,#4c6a3a 55%,#445564 72%,#33424c 100%)}
.video svg{position:absolute;left:233px;top:96px}

/* work */
.work-head{left:0;top:1524px;width:1200px;height:128px}
.work-head .section-title{margin-top:7px}
.filters{display:flex;justify-content:center;gap:30px;font-size:13px;margin-top:14px}
.filters .on{color:var(--blue)}
.grid{left:0;top:1652px;width:1200px;height:365px;display:grid;grid-template-columns:repeat(5,240px);grid-template-rows:182px 183px}
.tile{position:relative}
.tile.hover{background:#2b3440;color:#fff;text-align:center}
.tile.hover h4{font-size:19px;font-weight:400;margin-top:45px}
.tile.hover small{display:block;font-size:13px;margin-top:12px}
.tile.hover .acts{display:flex;justify-content:center;gap:22px;margin-top:18px}
.tile.hover .acts span{width:27px;height:27px;background:var(--blue);border-radius:3px}

/* partners */
.partners{left:0;top:2017px;width:1200px;height:157px;background:#fff}
.badge{position:absolute;top:70px;width:104px;height:22px;border-radius:11px;background:#d5d9dc}
.skyline{left:0;top:2107px;width:1200px;height:67px;background:linear-gradient(180deg,rgba(86,170,224,0) 0%,rgba(86,170,224,.65) 100%)}

/* footer */
.footer{left:0;top:2174px;width:1200px;height:394px;background:linear-gradient(90deg,var(--blue) 0%,var(--blue-light) 100%);color:#fff}
.footer h5{font-size:19px;font-weight:700;position:absolute}
.contact{left:48px;top:76px;width:260px;font-size:13px;line-height:20px}
.contact p{margin-bottom:14px}
.socials{display:flex;gap:12px}
.socials span{width:12px;height:12px;border-radius:50%;background:#fff}
.map{left:329px;top:72px;width:534px;height:211px;background:linear-gradient(135deg,#aad3e8 0%,#e7ecdd 45%,#a9d2e6 75%,#f1eee6 100%)}
.review{left:892px;top:72px;width:270px}
.review .quote{position:absolute;left:0;top:4px;font-size:58px;line-height:40px;color:rgba(255,255,255,.8);font-family:Georgia,serif}
.review p{margin-left:46px;font-size:13px;line-height:19.5px}
.avatar{position:absolute;left:0;top:110px;width:78px;height:78px;border-radius:50%;background:linear-gradient(160deg,#e8d2c2,#9b8678);border:3px solid #fff}
.who{position:absolute;left:92px;top:123px}
.who b{font-size:17px;font-weight:400;display:block}
.who small{font-size:12px;display:block;margin-top:12px}
.foot-rule{left:48px;top:336px;width:1100px;border-top:1px solid rgba(255,255,255,.6)}
.copy{left:0;top:364px;width:1200px;text-align:center;font-size:13px;font-weight:500}
</style>
</head>
<body>

<header>
  <div class="abs topbar">
    <div class="info">
      <span>&#9742; +1 800 555 01 25</span>
      <span>&#9993; info@pinecrestholdingsgroup.example</span>
      <span class="tag builders">Builders</span>
      <span class="tag renovators">Renovators</span>
    </div>
  </div>
  <div class="abs navband">
    <nav class="nav">
      <span>HOME</span><span>ABOUT US</span><span>OUR SERVICES</span><span>OUR WORKS</span><span>BLOG</span><span>CONTACT US</span>
    </nav>
  </div>
  <div class="abs brand">
    <span class="mark"></span>
    <span class="name">Pinecrest<br>Holdings Group</span>
  </div>
</header>

<section class="abs hero" role="img" aria-label="Lakeside villa with infinity pool overlooking mountains"></section>
<div class="abs hero-title">Investing in our neighborhoods<br>Pinecrest Holdings Group</div>
<div class="abs btn-hero" style="left:793px;width:78px">CALL NOW</div>
<div class="abs btn-hero" style="left:930px;width:105px">GO ON SURFING</div>
<div class="abs dots"><span class="off"></span><span></span><span></span><span></span></div>

<section class="abs welcome">
  <h1>Welcome We're Pinecrest Holdings Group</h1>
  <div class="rule"></div>
  <p>Pinecrest Holdings Group is a family run business with 3rd generation builders and renovators in the Morris County area. As the President and owner of Pinecrest Holdings Group I am dedicated to working hard to create opportunities for investment through real estate.</p>
  <p>At Pinecrest Holdings Group we have a valuable support system and a team of investors, realtors, attorneys, contractors and property managers providing a combined package offering years of experience in the local market.</p>
</section>

<section class="abs builders">
  <h2 class="section-title">Builders and <em>Renovators</em></h2>
  <div class="rule-blue"></div>

  <div class="abs feature" style="left:430px;left:430px;left:429px;left:429px;left:429px;left:429px;left:429px;left:429px;left:429px;left:429px;left:429px;left:429px;left:429px;left:429px;left:429px;left:429px;left:429px;left:429px;left:429px;left:429px;left:54px">
    <div class="icon"><svg width="40" height="40" viewBox="0 0 40 40" fill="none" stroke="#fff" stroke-width="2"><path d="M5 19 20 7l15 12"/><path d="M9 16v17h22V16"/><rect x="14" y="22" width="12" height="7" rx="2"/></svg></div>
    <h3>What we do</h3>
    <p>We are a team of experienced home buyers and renovators in the Morris County, NJ area. Our specialty is purchasing distressed homes and property. We then collaborate with the best talents in Northern New Jersey to renovate those properties and transform them into the best house in the neighborhood.</p>
  </div>

  <div class="abs feature" style="left:429px">
    <div class="icon"><svg width="40" height="40" viewBox="0 0 40 40" fill="none" stroke="#fff" stroke-width="2"><path d="M20 35s-10-11-10-19a10 10 0 0 1 20 0c0 8-10 19-10 19z"/><circle cx="20" cy="16" r="3.5"/></svg></div>
    <h3>Where we are</h3>
    <p>We only work in the Morris County area so we are local and know the area and market. We can finance or buy your home for cash. Our team will do any major renovations to the home or property and then make them available for rental or resale right here in our own neighborhoods.</p>
  </div>

  <div class="abs feature" style="left:804px">
    <div class="icon"><svg width="40" height="40" viewBox="0 0 40 40" fill="none" stroke="#fff" stroke-width="2"><path d="M10 5h14l7 7v23H10z"/><path d="M24 5v7h7M15 19h11M15 24h11M15 29h8"/></svg></div>
    <h3>Who we are</h3>
    <p>Pinecrest Holdings Group is a family run business with 3rd generation builders and renovators in the Morris County area. As the President and owner of Pinecrest Holdings Group I am dedicated to working hard to create opportunities for investment through real estate.</p>
  </div>
</section>

<section class="abs mail">
  <h2>Feel Free to Mail</h2>
  <div class="field" style="left:49px;top:86px;width:242px;height:33px">Name *</div>
  <div class="field" style="left:310px;top:86px;width:242px;height:33px">Email *</div>
  <div class="field" style="left:49px;top:138px;width:503px;height:33px">Subject</div>
  <div class="field" style="left:49px;top:190px;width:503px;height:57px;align-items:flex-start;padding-top:10px">Write Your Message Here...</div>
  <div class="abs send">SEND MESSAGE</div>
</section>

<section class="abs video" role="img" aria-label="Intro video still of a calm lake lined with trees">
  <svg width="132" height="132" viewBox="0 0 132 132"><circle cx="66" cy="66" r="61" fill="none" stroke="#fff" stroke-width="8"/><path d="M50 38v56l44-28z" fill="#fff"/></svg>
</section>

<section class="abs work-head">
  <h2 class="section-title">Our <em>Work</em></h2>
  <div class="rule-blue"></div>
  <div class="filters"><span class="on">All Works</span><span>Renovation house</span><span>Builder house</span></div>
</section>

<section class="abs grid">
  <div class="tile" role="img" aria-label="Two-storey house under renovation" style="background:linear-gradient(180deg,#b9c8d6,#6c7a84 60%,#57604c)"></div>
  <div class="tile" role="img" aria-label="Timber frame construction site in woods" style="background:linear-gradient(180deg,#9aa88c,#7a5b3e 60%,#4f3a28)"></div>
  <div class="tile hover">
    <h4>Integer Nec Odio</h4>
    <small>People</small>
    <div class="acts"><span></span><span></span></div>
  </div>
  <div class="tile" role="img" aria-label="Bungalow with front steps and garden" style="background:linear-gradient(180deg,#c7d3c0,#7d8a6a 55%,#4e5a3c)"></div>
  <div class="tile" role="img" aria-label="Small house on a cleared wooded lot" style="background:linear-gradient(180deg,#c9ccc8,#7f7c70 60%,#4f4a3c)"></div>
  <div class="tile" role="img" aria-label="Building supply store aisle" style="background:linear-gradient(180deg,#d8d8d8,#9a8a86 55%,#5b5a5e)"></div>
  <div class="tile" role="img" aria-label="Tree-lined driveway to a property" style="background:linear-gradient(180deg,#8fae7e,#5f7c49 55%,#6a6a62)"></div>
  <div class="tile" role="img" aria-label="Renovated blue two-storey house" style="background:linear-gradient(180deg,#a7cbe8,#4b5b6a 55%,#3d4a3a)"></div>
  <div class="tile" role="img" aria-label="House with new stone retaining wall" style="background:linear-gradient(180deg,#b8cde0,#9ea7a0 50%,#6f7a58)"></div>
  <div class="tile" role="img" aria-label="Finished grey family home with lawn" style="background:linear-gradient(180deg,#cfe0ea,#8e9993 50%,#5f7a40)"></div>
</section>

<section class="abs partners" aria-label="Partners">
  <span class="badge" style="left:78px"></span>
  <span class="badge" style="left:268px"></span>
  <span class="badge" style="left:453px"></span>
  <span class="badge" style="left:643px"></span>
  <span class="badge" style="left:829px"></span>
  <span class="badge" style="left:1019px"></span>
</section>
<div class="abs skyline" role="img" aria-label="City skyline silhouette with airplanes"></div>

<footer class="abs footer">
  <h5 style="left:48px;top:40px">Contact Us</h5>
  <div class="abs contact">
    <p>Please feel free to contact us for any issue. Our staff is available to you from 9AM until 5PM on weekdays.</p>
    <p><b>Phone:</b> +1 (800) 555 01 96</p>
    <p><b>Office:</b> 418 Alder Lane, Morristown</p>
    <p><b>Email:</b> info@pinecrestholdingsgroup.example</p>
    <div class="socials"><span></span><span></span><span></span><span></span><span></span></div>
  </div>

  <h5 style="left:547px;top:40px">Headquarters</h5>
  <div class="abs map" role="img" aria-label="Street map showing the office location"></div>

  <h5 style="left:892px;top:40px">Last Review</h5>
  <div class="abs review">
    <span class="quote">&ldquo;</span>
    <p>At vero eos et accusamus et iusto odio dignissimos ducimus qui blanditiis praesentium voluptatum deleniti atque corrupti quos dolores et quas molestias excepturi sint occaecati.</p>
    <div class="avatar" role="img" aria-label="Reviewer portrait"></div>
    <div class="who"><b>Evan Marsh</b><small>Developer</small></div>
  </div>

  <div class="abs foot-rule"></div>
  <div class="abs copy">Copyright 2020 - Pinecrest Holdings Group. All rights reserved.</div>
</footer>

</body>
</html>
```